BrimFalcon Business Cards

We have a defined brand. Please visit our website to get a feel for the product and the color pallets. www.brimfalcon-example.com

We need an updated, world class business card design. (See the attached existing card design). Please utilize BOTH sides of the card as shown and be creative with the layout. I do want the horse head icon to be positioned as it is with the existing card.

The remainder of the layout can be customized and I also want it vertically oriented.

Attached are the logo files and please use the colors as follows:
Green - #A5CE39
Tan - #CDBD99
Black

Feel free to play with the colors.

```html
<!DOCTYPE html>
<html lang="en">
<head>
<meta charset="utf-8">
<title>BrimFalcon Business Cards</title>
<link rel="stylesheet" href="https://fonts.googleapis.com/css2?family=Open+Sans:wght@400;600;700&display=swap">
<style>
  :root {
    --bg: #3b3b3b;
    --card: #ffffff;
    --ink: #1a1a1a;
    --muted: #444444;
    --green: #a5ce39;
    --green-deep: #3a9548;
    --green-bright: #c9da2c;
    --edge: #1f3590;
  }
  * { box-sizing: border-box; margin: 0; padding: 0; }
  html, body { width: 1200px; height: 900px; overflow: hidden; }
  body {
    background: var(--bg);
    font-family: "Open Sans", Arial, sans-serif;
    color: var(--ink);
    position: relative;
  }
  .card {
    position: absolute;
    left: 300px;
    width: 600px;
    height: 343px;
    background: var(--card);
    border-radius: 22px;
    overflow: hidden;
    box-shadow: 0 6px 0 var(--edge), 0 16px 30px rgba(0,0,0,.45);
  }
  .card--front { top: 70px; }
  .card--back { top: 480px; }

  .brand { display: flex; align-items: center; gap: 10px; }
  .brand__dot {
    width: 30px; height: 30px; border-radius: 50%;
    background: var(--ink);
  }
  .brand__name {
    font-weight: 700; font-size: 34px; letter-spacing: -0.5px;
    color: var(--ink); line-height: 1;
  }
  .brand__tagline {
    font-size: 11px; letter-spacing: 4px; color: var(--ink);
    margin: 4px 0 0 40px;
  }
  .card--front .brand-block { position: absolute; left: 34px; top: 34px; }
  .card--front .brand__name { font-size: 28px; }
  .card--front .brand__dot { width: 26px; height: 26px; }
  .card--front .brand__tagline { font-size: 9px; letter-spacing: 3.4px; margin-left: 36px; }

  .card--back .brand-block {
    position: absolute; left: 50%; top: 50%;
    transform: translate(-50%, -50%);
  }
  .card--back .brand__name { font-size: 42px; }
  .card--back .brand__dot { width: 38px; height: 38px; }
  .card--back .brand__tagline { font-size: 13px; letter-spacing: 5px; margin-left: 48px; }

  .swoosh { position: absolute; inset: 0; width: 600px; height: 343px; }

  .person { position: absolute; left: 300px; top: 112px; }
  .person__name {
    color: var(--green); font-weight: 600; font-size: 18px;
    letter-spacing: 5px; text-transform: uppercase;
  }
  .person__title { font-size: 8px; color: var(--muted); margin-top: 1px; }

  .contact { position: absolute; left: 260px; top: 168px; list-style: none; }
  .contact__item {
    display: flex; align-items: center; gap: 8px;
    font-size: 14px; color: var(--muted); line-height: 21px;
  }
  .contact__icon { width: 14px; height: 14px; fill: var(--green); flex: none; }

  .address {
    position: absolute; right: 26px; bottom: 16px;
    font-size: 11.5px; line-height: 15px; color: var(--ink); text-align: right;
  }
</style>
</head>
<body>

  <section class="card card--front" aria-label="Card front">
    <svg class="swoosh" viewBox="0 0 600 343" aria-hidden="true">
      <defs>
        <linearGradient id="band" x1="0" y1="0" x2="1" y2="0">
          <stop offset="0" stop-color="#3a9548"/>
          <stop offset="0.45" stop-color="#c9da2c"/>
          <stop offset="1" stop-color="#3a9548"/>
        </linearGradient>
      </defs>
      <path d="M0,222 C120,240 200,320 330,318 C420,316 500,278 600,262 L600,343 L0,343 Z" fill="url(#band)"/>
      <path d="M0,200 C130,214 220,296 340,298 C430,298 500,264 570,246 C505,276 430,310 335,311 C205,312 125,236 0,215 Z" fill="#111111"/>
    </svg>

    <div class="brand-block">
      <div class="brand">
        <span class="brand__dot"></span>
        <span class="brand__name">BrimFalcon</span>
      </div>
      <p class="brand__tagline">Performance Driven EVs</p>
    </div>

    <div class="person">
      <p class="person__name">Dana Reyes</p>
      <p class="person__title">CEO/Managing Director</p>
    </div>

    <ul class="contact">
      <li class="contact__item">
        <svg class="contact__icon" viewBox="0 0 24 24" aria-hidden="true"><path d="M6.6 10.8a15.1 15.1 0 0 0 6.6 6.6l2.2-2.2c.3-.3.7-.4 1-.2 1.1.4 2.3.6 3.6.6.6 0 1 .4 1 1V20c0 .6-.4 1-1 1A17 17 0 0 1 3 4c0-.6.4-1 1-1h3.5c.6 0 1 .4 1 1 0 1.3.2 2.5.6 3.6.1.3 0 .7-.2 1z"/></svg>
        555-010-2288
      </li>
      <li class="contact__item">
        <svg class="contact__icon" viewBox="0 0 24 24" aria-hidden="true"><path d="M6 2h10v6H6zM3 9h18v10h-3v3H6v-3H3zm5 8v3h8v-3z"/></svg>
        555-010-2288
      </li>
      <li class="contact__item">
        <svg class="contact__icon" viewBox="0 0 24 24" aria-hidden="true"><path d="M2 5h20v14H2zm2 2v.5l8 5.5 8-5.5V7z"/></svg>
        dana.reyes@brimfalcon-example.com
      </li>
    </ul>

    <p class="address">410 Harbor Street NW<br>Suite 200, Fairview MI 49000</p>
  </section>

  <section class="card card--back" aria-label="Card back">
    <div class="brand-block">
      <div class="brand">
        <span class="brand__dot"></span>
        <span class="brand__name">BrimFalcon</span>
      </div>
      <p class="brand__tagline">Performance Driven EVs</p>
    </div>
  </section>

</body>
</html>
```